Ft Darrow Cider Co needs web page design

Need a web design for a ecommerce website for honey wine. We make honeywine (a dessert type wine made with honey). Our initial product is a standard honey wine and pyment and a cyser. We have all our logos and designs but need to place in web design to reflect our product and ecommerce. We want the file labeled "chatwave cover logo 2" as the banner for the site.

Target Market(s)

People who drink sweeter wines, dessert wine, or non traditional/non-grape wines. Cizer drinkers. 20-60 years old.

Requirements
Must have
• The "bee button" picture as the button image. The "cw cover 2" image as the page banner. Open, bright feel/coloring. Coloring featuring gold, red colors that reflect our logos. PLEASE USE THE CHATWAVE COVER 2 AS OR ON LABEL BANNER TOP OF WEB PAGE. Files 2-3-4 and 5 are our first labels. Those are what will be on bottles when we sale them. This should reflect on web page. We will not use file 8 labels but the graphics could be used on website. There for inspiration.
Nice to have
• Reflect the fonts that are on our logos as close as possible.
Should not have
• Not too much black, red, or honey references. We don't want the page to be too saturated with any of those elements. Not cluttered with imagery.

```html
<!DOCTYPE html>
<html lang="en">
<head>
<meta charset="utf-8">
<title>Ft Darrow Cider Co</title>
<link href="https://fonts.googleapis.com/css2?family=Cinzel:wght@400;600&family=Open+Sans:ital,wght@0,400;0,600;0,700;1,400&display=swap" rel="stylesheet">
<style>
:root{
  --crimson:#9b1b30;
  --crimson-deep:#8a1a2d;
  --orange:#f6a21c;
  --gold:#c9a13b;
  --ink:#2a2a2a;
  --charcoal:#2b2b2b;
  --text:#7a7a7a;
  --mist:#f7f7f7;
  --night:#161616;
  --white:#ffffff;
}
*{margin:0;padding:0;box-sizing:border-box}
html,body{width:1200px;height:4831px;overflow:hidden}
body{position:relative;background:var(--white);font-family:"Open Sans",Arial,sans-serif;color:var(--ink)}
.section{position:absolute;left:0;width:1200px}
.abs{position:absolute}

/* header */
.site-header{top:0;height:124px;background:var(--white)}
.brand{left:112px;top:62px;font-family:"Open Sans",Arial,sans-serif;font-weight:600;font-size:25px;line-height:30px;color:var(--crimson);white-space:nowrap}
.topline{right:112px;top:16px;font-size:14px;color:#555;display:flex;gap:10px;align-items:center}
.topline svg{width:13px;height:13px}
.nav{left:418px;top:76px;display:flex;font-family:"Cinzel",Georgia,serif;font-size:15px;color:#333}
.nav span{margin-right:27px}
.nav .active{color:var(--orange)}
.tool{top:62px;width:44px;height:44px;border-radius:50%;border:1.5px solid #333;display:flex;align-items:center;justify-content:center}
.tool svg{width:16px;height:16px}
.tool.cart{background:var(--orange);border-color:var(--orange)}

/* hero */
.hero{top:124px;height:588px;overflow:hidden}
.hero-photo{position:absolute;inset:0;background:linear-gradient(180deg,#3f7fc4 0%,#7bb0e0 32%,#b9cfe0 45%,#7e8b5e 58%,#5a6d3a 75%,#b7a07a 92%)}
.hero h1{position:absolute;top:72px;width:100%;text-align:center;font-family:"Cinzel",Georgia,serif;font-weight:400;font-size:68px;color:var(--white);letter-spacing:1px}
.hero .tagline{position:absolute;top:158px;width:100%;text-align:center;font-size:28px;font-weight:600;color:var(--white)}
.hero-curve{position:absolute;left:0;top:488px;width:1200px;height:100px}

/* buttons */
.btn{display:flex;align-items:center;background:var(--charcoal);color:var(--white);border-radius:30px;height:57px;width:180px;font-size:16px;font-weight:600;padding-left:6px}
.btn .coin{width:48px;height:48px;border-radius:50%;background:radial-gradient(circle at 40% 35%,#efd68a,#c9a13b 55%,#8c6a22);margin-right:14px;flex:none}

/* welcome */
.welcome{top:712px;height:550px}
.sec-title{font-family:"Cinzel",Georgia,serif;font-weight:400;font-size:42px;color:#333;line-height:48px}
.body-copy{font-size:16px;line-height:28px;color:var(--text)}
.story-photo{left:673px;top:53px;width:435px;height:418px;background:linear-gradient(135deg,#8a6a4a,#c9b49a 45%,#6b5240)}
.story-tag{left:636px;top:29px;width:107px;height:92px;background:var(--orange);color:var(--white);font-size:21px;line-height:26px;text-align:center;padding-top:20px}

/* products */
.product h2{font-family:"Cinzel",Georgia,serif;font-weight:400;font-size:42px;color:#333}
.price{font-size:34px;font-weight:700;color:#333}
.feature{position:absolute;width:140px;text-align:center;font-size:16px;line-height:20px;color:#333}
.feature .ring{width:90px;height:90px;margin:0 auto 14px;border-radius:50%;border:3px solid var(--crimson);display:flex;align-items:center;justify-content:center}
.feature .ring span{width:74px;height:74px;border-radius:50%;border:2px solid var(--orange);display:flex;align-items:center;justify-content:center}
.feature svg{width:40px;height:40px}
.product-shot{position:absolute}
.shot-gold{background:linear-gradient(135deg,#3a3530 0%,#5b4a32 45%,#d9b860 100%)}
.shot-red{background:linear-gradient(135deg,#8c2a40 0%,#3a3032 45%,#b3283a 100%)}
.shot-apple{background:linear-gradient(135deg,#b8342c 0%,#3a3530 40%,#d9b860 100%)}
.honey{top:1262px;height:542px;background:var(--mist)}
.pyment{top:1804px;height:544px;background:var(--white)}
.cyser{top:2348px;height:549px;background:var(--mist)}

/* blog */
.blog{top:2897px;height:549px}
.center-title{position:absolute;width:100%;text-align:center}
.card{position:absolute;top:139px;width:311px;height:380px}
.card .thumb{position:absolute;left:0;top:0;width:311px;height:212px}
.date{position:absolute;left:28px;top:180px;width:45px;height:56px;background:var(--crimson);color:var(--white);text-align:center;font-size:20px;font-weight:700;line-height:22px;padding-top:6px}
.date small{display:block;font-size:14px;font-weight:400}
.card h3{position:absolute;top:244px;font-size:22px;font-weight:600;color:#333;letter-spacing:.3px;white-space:nowrap}
.card p{position:absolute;top:281px;font-size:15px;line-height:26px;color:var(--text)}

/* testimonials */
.testimonials{top:3446px;height:469px;background:linear-gradient(180deg,var(--crimson) 0%,var(--crimson-deep) 60%,#95313f 100%)}
.quote{position:absolute;top:137px;left:0;width:100%;text-align:center;font-style:italic;font-size:23px;line-height:33px;color:var(--white)}
.author{position:absolute;top:290px;width:100%;text-align:center;font-size:19px;color:var(--white)}
.dots{position:absolute;top:377px;left:550px;display:flex;gap:8px}
.dots i{width:28px;height:4px;background:rgba(255,255,255,.45)}
.dots i:first-child{background:var(--white)}

/* gallery */
.gallery{top:3915px;height:435px}
.tile{position:absolute;top:148px;width:238px;height:227px}

/* footer */
.site-footer{top:4350px;height:481px}
.footer-curve{position:absolute;left:0;top:0;width:1200px;height:481px}
.f-brand{left:112px;top:196px;font-family:"Open Sans",Arial,sans-serif;font-weight:600;font-size:28px;line-height:34px;color:var(--white);white-space:nowrap}
.f-contact{left:112px;font-size:16px;font-weight:600;color:var(--white);display:flex;align-items:center;gap:12px}
.f-contact svg{width:14px;height:14px}
.f-head{font-family:"Cinzel",Georgia,serif;font-size:20px;color:var(--white);letter-spacing:.5px}
.f-links{left:508px;top:168px;font-size:16px;line-height:29px;color:var(--white)}
.f-note{left:720px;top:168px;width:340px;font-size:16px;line-height:22px;color:var(--white)}
.f-input{left:720px;top:229px;width:368px;height:52px;background:var(--white);font-size:16px;color:#777;padding:14px 18px}
.f-btn{left:720px;top:302px;width:158px;height:54px;border-radius:27px;background:var(--orange);color:var(--white);font-size:15px;font-weight:600;text-align:center;line-height:54px}
.f-rule{left:0;top:403px;width:1200px;height:1px;background:#3a3a3a}
.copyright{left:112px;top:417px;font-size:16px;color:var(--white)}
.social{top:421px;width:36px;height:36px;border-radius:50%;border:1.5px solid var(--white);color:var(--white);font-size:12px;font-weight:600;text-align:center;line-height:33px}
</style>
</head>
<body>

<header class="section site-header">
  <div class="abs brand">Ft Darrow Cider Co</div>
  <div class="abs topline">
    <svg viewBox="0 0 24 24" fill="#f6a21c"><path d="M6.6 10.8a15 15 0 0 0 6.6 6.6l2.2-2.2c.3-.3.7-.4 1-.2 1.1.4 2.3.6 3.6.6.6 0 1 .4 1 1V20c0 .6-.4 1-1 1C10.6 21 3 13.4 3 4c0-.6.4-1 1-1h3.5c.6 0 1 .4 1 1 0 1.3.2 2.5.6 3.6.1.3 0 .7-.2 1z"/></svg>
    <span>1 (555) 014-2290</span><span>|</span>
    <svg viewBox="0 0 24 24" fill="#f6a21c"><path d="M2 5h20v14H2z"/><path d="M2 5l10 8 10-8" fill="none" stroke="#fff" stroke-width="2"/></svg>
    <span>hello@ftdarrowcider.example</span>
  </div>
  <nav class="abs nav"><span class="active">HOME</span><span>OUR STORY</span><span>OUR CIDERS</span><span>BLOG</span><span>CONTACT US</span></nav>
  <div class="abs tool" style="left:942px"><svg viewBox="0 0 24 24" fill="none" stroke="#222" stroke-width="3"><circle cx="10" cy="10" r="6"/><path d="M15 15l6 6"/></svg></div>
  <div class="abs tool" style="left:992px"><svg viewBox="0 0 24 24" fill="#222"><circle cx="12" cy="8" r="5"/><path d="M3 22c0-6 4-8 9-8s9 2 9 8z"/></svg></div>
  <div class="abs tool cart" style="left:1043px"><svg viewBox="0 0 24 24" fill="#fff"><path d="M2 3h4l3 11h10l3-8H8" stroke="#fff" stroke-width="2" fill="none"/><circle cx="10" cy="19" r="2"/><circle cx="18" cy="19" r="2"/></svg></div>
</header>

<section class="section hero">
  <div class="hero-photo" role="img" aria-label="Blue sky over green rolling hills and a valley town"></div>
  <h1>FT DARROW CIDER</h1>
  <p class="tagline">Made from 100% natural honey!</p>
  <div class="btn abs" style="left:510px;top:225px"><span class="coin" role="img" aria-label="Gold coin button image"></span>SHOP NOW!</div>
  <svg class="hero-curve" viewBox="0 0 1200 100" preserveAspectRatio="none">
    <path d="M0,80 Q600,10 1200,86 L1200,100 L0,100 Z" fill="#9b1b30"/>
    <path d="M0,92 Q600,42 1200,96 L1200,100 L0,100 Z" fill="#ffffff"/>
  </svg>
</section>

<section class="section welcome">
  <h2 class="abs sec-title" style="left:108px;top:97px">WELCOME TO<br>FTDARROW CIDER CO</h2>
  <p class="abs body-copy" style="left:110px;top:208px;width:490px">At vero eos et accusamus et iusto odio dignissimos ducimus qui blanditiis praesentium voluptatum de niti atque corrupti quosis dolores et quas molestias excepturi sint occaecati cupiditatesen provident, simili que sunt in culpa qui officia deserunt mollitiain imi, id est laborum et dolorum fuga.</p>
  <div class="btn abs" style="left:111px;top:377px"><span class="coin" role="img" aria-label="Gold coin button image"></span>READ MORE</div>
  <div class="abs story-photo" role="img" aria-label="Smiling older winemaker raising a glass of wine in a cellar"></div>
  <div class="abs story-tag">OUR<br>STORY</div>
</section>

<section class="section product honey">
  <div class="product-shot shot-gold" style="left:30px;top:12px;width:460px;height:530px" role="img" aria-label="Honey wine bottle beside a glass of golden wine and honeycomb"></div>
  <h2 class="abs" style="left:594px;top:56px">HONEY WINE</h2>
  <div class="abs price" style="left:594px;top:114px">$149</div>
  <p class="abs body-copy" style="left:596px;top:168px;width:500px">At vero eos et accusamus et iusto odio dignissimos ducimus qui blanditiis praesentium voluptatum de.</p>
  <div class="feature" style="left:569px;top:242px"><div class="ring"><span><svg viewBox="0 0 40 40"><path d="M8 32C8 16 20 8 34 8c0 16-10 24-26 24z" fill="#f6a21c"/></svg></span></div>Natural<br>Ingredients</div>
  <div class="feature" style="left:721px;top:242px"><div class="ring"><span><svg viewBox="0 0 40 40"><path d="M20 4l14 8v16l-14 8-14-8V12z" fill="#f6a21c"/></svg></span></div>100% natural<br>honey</div>
  <div class="feature" style="left:871px;top:242px"><div class="ring"><span><svg viewBox="0 0 40 40" fill="none" stroke="#f6a21c" stroke-width="3"><circle cx="20" cy="20" r="16"/><path d="M9 31L31 9M20 10v22"/></svg></span></div>Gluten<br>Free</div>
  <div class="btn abs" style="left:596px;top:412px"><span class="coin" role="img" aria-label="Gold coin button image"></span>SHOP NOW!</div>
</section>

<section class="section product pyment">
  <div class="abs" style="left:780px;top:-20px;width:440px;height:440px;border-radius:50%;background:#f7f7f7"></div>
  <h2 class="abs" style="left:112px;top:56px">PYMENT</h2>
  <div class="abs price" style="left:112px;top:108px">$149</div>
  <p class="abs body-copy" style="left:114px;top:162px;width:490px">At vero eos et accusamus et iusto odio dignissimos ducimus qui blanditiis praesentium voluptatum de.</p>
  <div class="feature" style="left:88px;top:236px"><div class="ring"><span><svg viewBox="0 0 40 40" fill="#f6a21c"><circle cx="14" cy="12" r="5"/><circle cx="26" cy="12" r="5"/><circle cx="20" cy="20" r="5"/><circle cx="12" cy="22" r="4"/><circle cx="28" cy="22" r="4"/><circle cx="20" cy="30" r="5"/></svg></span></div>Fresh<br>Grapes</div>
  <div class="feature" style="left:239px;top:236px"><div class="ring"><span><svg viewBox="0 0 40 40"><path d="M20 4l14 8v16l-14 8-14-8V12z" fill="#f6a21c"/></svg></span></div>100% natural<br>honey</div>
  <div class="feature" style="left:389px;top:236px"><div class="ring"><span><svg viewBox="0 0 40 40" fill="none" stroke="#f6a21c" stroke-width="3"><circle cx="20" cy="20" r="16"/><path d="M9 31L31 9M20 10v22"/></svg></span></div>Gluten<br>Free</div>
  <div class="btn abs" style="left:112px;top:410px"><span class="coin" role="img" aria-label="Gold coin button image"></span>SHOP NOW!</div>
  <div class="product-shot shot-red" style="left:660px;top:16px;width:380px;height:528px" role="img" aria-label="Pyment bottle beside a glass of red wine and a bunch of red grapes"></div>
</section>

<section class="section product cyser">
  <div class="product-shot shot-apple" style="left:20px;top:20px;width:470px;height:529px" role="img" aria-label="Cyser bottle beside a glass of pale wine and a halved red apple"></div>
  <h2 class="abs" style="left:602px;top:67px">CYSER</h2>
  <div class="abs price" style="left:602px;top:123px">$149</div>
  <p class="abs body-copy" style="left:605px;top:177px;width:500px">At vero eos et accusamus et iusto odio dignissimos ducimus qui blanditiis praesentium voluptatum de.</p>
  <div class="feature" style="left:579px;top:249px"><div class="ring"><span><svg viewBox="0 0 40 40" fill="#f6a21c"><circle cx="20" cy="23" r="13"/><path d="M20 10c0-4 3-6 6-6" stroke="#f6a21c" stroke-width="3" fill="none"/></svg></span></div>Fresh<br>Apples</div>
  <div class="feature" style="left:731px;top:249px"><div class="ring"><span><svg viewBox="0 0 40 40"><path d="M20 4l14 8v16l-14 8-14-8V12z" fill="#f6a21c"/></svg></span></div>100% natural<br>honey</div>
  <div class="feature" style="left:881px;top:249px"><div class="ring"><span><svg viewBox="0 0 40 40" fill="none" stroke="#f6a21c" stroke-width="3"><circle cx="20" cy="20" r="16"/><path d="M9 31L31 9M20 10v22"/></svg></span></div>Gluten<br>Free</div>
  <div class="btn abs" style="left:606px;top:420px"><span class="coin" role="img" aria-label="Gold coin button image"></span>SHOP NOW!</div>
</section>

<section class="section blog">
  <h2 class="center-title sec-title" style="top:62px">LATEST BLOG</h2>
  <article class="card" style="left:111px">
    <div class="thumb" role="img" aria-label="Glasses of white wine and bottles on a wooden table" style="background:linear-gradient(135deg,#5a3a1e,#c9a24c 50%,#3d2813)"></div>
    <div class="date">10<small>MAY</small></div>
    <h3>Ut enim ad minima venia</h3>
    <p>Nemo enim ipsam voluptatem quia volu ptas sit aspernatur aut odit.</p>
  </article>
  <article class="card" style="left:444px">
    <div class="thumb" role="img" aria-label="Vineyard rows at sunset" style="background:linear-gradient(180deg,#c9662a,#f1a44a 40%,#7a4a1e 65%,#4a3414)"></div>
    <div class="date">10<small>MAY</small></div>
    <h3>Ut enim ad minima venia</h3>
    <p>Nemo enim ipsam voluptatem quia volu ptas sit aspernatur aut odit.</p>
  </article>
  <article class="card" style="left:778px">
    <div class="thumb" role="img" aria-label="Red apples in a basket beside a glass of cider" style="background:linear-gradient(135deg,#e7e2d4,#b2253a 40%,#e9c75a 70%,#f1ede0)"></div>
    <div class="date">10<small>MAY</small></div>
    <h3>Ut enim ad minima venia</h3>
    <p>Nemo enim ipsam voluptatem quia volu ptas sit aspernatur aut odit.</p>
  </article>
</section>

<section class="section testimonials" aria-label="Client testimonials over a faint crimson hillside backdrop">
  <h2 class="center-title sec-title" style="top:64px;color:#fff">CLIENT TESTIMONIALS</h2>
  <p class="quote">“ Nam libero tempore, cum soluta nobis est eligendi optio cum<br>nihil impedit quo minus id quod maxime placeat facere possimus, om<br>nis voluptas assumenda est, omnis dolor repellendus. Temporibus<br>autem quibusdam et aut officiis debitis au.”</p>
  <p class="author">- WALTER BRANDT</p>
  <div class="dots"><i></i><i></i><i></i></div>
</section>

<section class="section gallery">
  <h2 class="center-title sec-title" style="top:66px">#FTDARROWCIDER</h2>
  <div class="tile" style="left:111px;background:linear-gradient(180deg,#b7cbe0,#6b8a3a 40%,#3f5a22)" role="img" aria-label="Vineyard rows under a hazy sky"></div>
  <div class="tile" style="left:358px;background:linear-gradient(135deg,#2a0a0e,#b1182a 50%,#3a0a10)" role="img" aria-label="Red wine being poured into a glass"></div>
  <div class="tile" style="left:604px;background:linear-gradient(135deg,#3a5a2a,#2c3a6a 45%,#1a2240)" role="img" aria-label="Bunch of dark grapes on the vine"></div>
  <div class="tile" style="left:851px;background:linear-gradient(135deg,#d8d8d8,#9a5a44 50%,#6a6a6a)" role="img" aria-label="Winemaker tasting beside steel tanks"></div>
</section>

<footer class="section site-footer">
  <svg class="footer-curve" viewBox="0 0 1200 481" preserveAspectRatio="none">
    <path d="M0,4 Q600,60 1200,4 L1200,481 L0,481 Z" fill="#9b1b30"/>
    <path d="M0,26 Q600,80 1200,26 L1200,481 L0,481 Z" fill="#161616"/>
  </svg>
  <div class="abs f-brand">Ft Darrow Cider Co</div>
  <div class="abs f-contact" style="top:262px"><svg viewBox="0 0 24 24" fill="#f6a21c"><path d="M6.6 10.8a15 15 0 0 0 6.6 6.6l2.2-2.2c.3-.3.7-.4 1-.2 1.1.4 2.3.6 3.6.6.6 0 1 .4 1 1V20c0 .6-.4 1-1 1C10.6 21 3 13.4 3 4c0-.6.4-1 1-1h3.5c.6 0 1 .4 1 1 0 1.3.2 2.5.6 3.6.1.3 0 .7-.2 1z"/></svg>1 (555) 014-2290 &nbsp;|</div>
  <div class="abs f-contact" style="top:298px"><svg viewBox="0 0 24 24" fill="#f6a21c"><path d="M2 5h20v14H2z"/><path d="M2 5l10 8 10-8" fill="none" stroke="#161616" stroke-width="2"/></svg>hello@ftdarrowcider.example</div>
  <div class="abs f-head" style="left:508px;top:128px">INFORMATION</div>
  <div class="abs f-links">Home<br>Our Story<br>Our Ciders<br>Blog<br>Contact</div>
  <div class="abs f-head" style="left:720px;top:128px">NEWSLETTER SUBSCRIPTION</div>
  <p class="abs f-note">Subscribe and stay on top of our latest news and promotions</p>
  <div class="abs f-input">Email Address</div>
  <div class="abs f-btn">SUBSCRIBE</div>
  <div class="abs f-rule"></div>
  <p class="abs copyright">Copyright © 2021, Ft Darrow Cider Co. All rights reserved.</p>
  <div class="abs social" style="left:961px">cw</div>
  <div class="abs social" style="left:1008px">pp</div>
  <div class="abs social" style="left:1053px">sg</div>
</footer>

</body>
</html>
```